Computer Training in the Education sector - Letterhead

We need a new letter head to be designed for the company. We provide computer training fro the Education Sector, both primary and private tertiary providers. The colours will need to tie in with the website www.crossingthestream.co.nz.
The company name is Crossing the Stream with the tag line of Computer Training for Educators.
The footer will need to have the following detail...
0508 PCS MENTOR
021 839 415
www.crossingthestream.co.nz / training@crossingthestream.co.nz
Updates

Thanks for the designs so far.

Some have watermarks in the background. Please don't worry about using watermarks as I will not be using a watermark in in a final design.
Regards,
Roger

Thank you for all the designs and the effort. There was some great concepts that came through.

Cheers
Roger

Industry/Entity Type

Computer

```html
<!DOCTYPE html>
<html lang="en">
<head>
<meta charset="utf-8">
<title>Crossing the Stream – Letterhead</title>
<link rel="stylesheet" href="https://fonts.googleapis.com/css2?family=EB+Garamond:wght@400;500&display=swap">
<style>
  :root {
    --paper: #ffffff;
    --brand-blue: #2f76b9;
    --brand-orange: #e0893a;
    --ink: #3a3a3a;
    --rule: #6d6d6d;
  }
  * { margin: 0; padding: 0; box-sizing: border-box; }
  html, body {
    width: 1034px;
    height: 1200px;
    overflow: hidden;
    background: var(--paper);
  }
  .letterhead {
    position: relative;
    width: 1034px;
    height: 1200px;
    background: var(--paper);
    font-family: "EB Garamond", Georgia, serif;
    color: var(--ink);
  }
  .brand {
    position: absolute;
    left: 56px;
    top: 44px;
    display: flex;
    align-items: center;
    gap: 14px;
  }
  .brand-dot {
    width: 22px;
    height: 22px;
    border-radius: 50%;
    background: var(--brand-orange);
    flex: none;
  }
  .brand-name {
    font-weight: 500;
    font-size: 36px;
    line-height: 1.02;
    color: var(--brand-blue);
  }
  .contact {
    position: absolute;
    left: 711px;
    top: 56px;
    padding-left: 18px;
    border-left: 1.5px solid var(--rule);
    list-style: none;
    font-size: 16px;
    line-height: 22.5px;
  }
  .contact li {
    display: flex;
    align-items: center;
    gap: 8px;
    white-space: nowrap;
  }
  .contact svg {
    width: 13px;
    height: 13px;
    flex: none;
    fill: none;
    stroke: var(--ink);
    stroke-width: 1.6;
  }
  .footer-band {
    position: absolute;
    left: 0;
    top: 1100px;
    width: 1034px;
    height: 100px;
    display: block;
  }
  .footer-band .sweep { fill: var(--brand-orange); }
  .footer-band .band { fill: var(--brand-blue); }
  .tagline {
    position: absolute;
    left: 0;
    right: 0;
    top: 1136px;
    text-align: center;
    color: #ffffff;
    font-size: 23px;
    letter-spacing: 2px;
  }
</style>
</head>
<body>
  <main class="letterhead">
    <header>
      <div class="brand">
        <span class="brand-dot" aria-hidden="true"></span>
        <div class="brand-name">Crossing<br>the Stream</div>
      </div>

      <ul class="contact">
        <li>
          <svg viewBox="0 0 14 14" aria-hidden="true"><circle cx="7" cy="7" r="6"/><path d="M5 4l1.2 1.5-.8 1 1.8 2 1-.7L9.7 9.3 8.8 10.3C6.8 10 4.4 7.5 4 5.2z"/></svg>
          <span>0508 PCS MENTOR</span>
        </li>
        <li>
          <svg viewBox="0 0 14 14" aria-hidden="true"><circle cx="7" cy="7" r="6"/><path d="M5 4l1.2 1.5-.8 1 1.8 2 1-.7L9.7 9.3 8.8 10.3C6.8 10 4.4 7.5 4 5.2z"/></svg>
          <span>021 839 415</span>
        </li>
        <li>
          <svg viewBox="0 0 14 14" aria-hidden="true"><rect x="1.5" y="4" width="11" height="7.5"/><path d="M1.5 4L7 8l5.5-4"/></svg>
          <span>training@crossingthestream.co.nz</span>
        </li>
        <li>
          <svg viewBox="0 0 14 14" aria-hidden="true"><circle cx="7" cy="7" r="5.8"/><ellipse cx="7" cy="7" rx="2.5" ry="5.8"/><path d="M1.2 7h11.6M2 4h10M2 10h10"/></svg>
          <span>www.crossingthestream.co.nz</span>
        </li>
      </ul>
    </header>

    <footer>
      <svg class="footer-band" viewBox="0 0 1034 100" preserveAspectRatio="none" aria-hidden="true">
        <path class="sweep" d="M0 52 Q517 -36 1034 52 Q517 -22 0 52 Z"/>
        <path class="band" d="M0 64 Q517 -32 1034 64 V100 H0 Z"/>
      </svg>
      <p class="tagline">Computer Training for Educators</p>
    </footer>
  </main>
</body>
</html>
```